Data Analysis new tech startup

Design a simple / modern website (one page, one language) with a tech touch, based on the words prediction and/or IoT (Internet of Things).

VORMAL IoT is dedicated for Data Analysis of IoT or M2M (Machine to Machine) projects.

The website should follow the colors of the logo (see images)

The web site should look like this example: https://talvimetrics.example/en/ with less human pictures and ALL the text content should be configurable for later change.

The website will be published on a php web server.

Target Market(s)

Business professionals

Industry/Entity Type

Data Science

Coding

Coded - Design and coding required

Number of Pages Required

1 page

Colors

Designer to choose colors to be used in the design.

Requirements
Must have
• Follow example site guidelines (https://talvimetrics.example/en/)
• Follow logo colors
• Fun and startup look and feel
• ALL TEXT SHOULD BE CONFIGURABLE
• Clients carrousel with colored hovering
Nice to have
• Configurable photo carrousel at the top (after menu)
Should not have
• Too many human photos, just a few.

```html
<!DOCTYPE html>
<html lang="en">
<head>
<meta charset="utf-8">
<title>VORMAL IoT – Data Science</title>
<link rel="stylesheet" href="https://fonts.googleapis.com/css2?family=Montserrat:wght@400;500;600;700;800&display=swap">
<style>
:root{
  --violet:#9a3cf2;
  --indigo:#5a63f2;
  --blue:#4d7cf3;
  --pink:#f2346a;
  --rose:#e9307d;
  --ink:#2b2b33;
  --muted:#8a8a96;
  --soft:#f4f4f7;
  --footer-a:#6710c8;
  --footer-b:#9422d6;
  --white:#ffffff;
}
*{box-sizing:border-box;margin:0;padding:0}
html,body{width:1200px;height:4532px;overflow:hidden;background:#ffffff;font-family:"Montserrat",sans-serif;color:var(--ink)}
.page{position:absolute;left:48px;top:933px;width:1104px;height:2665px;background:var(--white);box-shadow:0 10px 40px rgba(60,40,120,.12);overflow:hidden}
section,header,footer{position:relative;width:1104px;overflow:hidden}
.abs{position:absolute}

/* hero */
.hero{height:613px;background:linear-gradient(115deg,var(--violet) 0%,#7d52f2 55%,var(--blue) 100%)}
.hero-curve{position:absolute;left:0;bottom:0;width:1104px;height:140px}
.topbar{left:0;top:0;width:1104px;height:42px;border-bottom:1px solid rgba(255,255,255,.25);display:flex;align-items:center;justify-content:space-between;padding:0 85px}
.social{display:flex;gap:8px}
.social span{width:10px;height:10px;border-radius:50%;background:rgba(255,255,255,.85)}
.contact-line{display:flex;gap:22px;color:rgba(255,255,255,.85);font-size:10px}
.brand{left:85px;top:76px;color:var(--white)}
.brand-name{font-size:27px;font-weight:700;letter-spacing:.5px;color:var(--white)}
.nav{right:85px;top:64px;display:flex;align-items:center;gap:30px;font-size:10px;font-weight:600;color:var(--white)}
.nav .active{border:1.5px solid var(--white);border-radius:20px;padding:8px 20px}
.hero-title{left:85px;top:250px;font-size:44px;font-weight:800;letter-spacing:2px;color:var(--white)}
.hero-copy{left:85px;top:310px;width:400px;font-size:11px;line-height:1.45;color:rgba(255,255,255,.85)}
.hero-art{left:460px;top:110px;width:620px;height:500px;border-radius:30px;background:radial-gradient(circle at 55% 45%,rgba(255,255,255,.35),rgba(120,110,245,.25) 55%,rgba(255,255,255,0) 72%)}

/* shared headings */
.ghost{font-size:84px;font-weight:800;color:#f1f1f4;white-space:nowrap}
.h2{font-size:40px;font-weight:700;color:var(--ink)}
.lead{font-size:11px;font-weight:700;line-height:1.55;color:#44444e}
.body{font-size:10px;line-height:1.6;color:var(--muted)}

/* methodology */
.method{height:476px}
.method .ghost{left:0;top:50px}
.method .h2{left:85px;top:126px}
.method .lead{left:85px;top:184px;width:445px}
.method .body{left:85px;top:240px;width:440px}
.method-grid{left:613px;top:86px;display:grid;grid-template-columns:196px 196px;gap:14px}
.m-card{height:140px;border-radius:10px;border:1.5px solid #d9c7fb;box-shadow:0 4px 14px rgba(140,90,240,.15);background:var(--white);text-align:center;padding:20px 14px 0}
.m-card.active{background:linear-gradient(135deg,var(--violet),var(--indigo));border-color:transparent;color:var(--white)}
.m-card svg{width:36px;height:36px}
.m-card h3{font-size:11px;font-weight:700;margin:8px 0 5px}
.m-card p{font-size:8.5px;line-height:1.45;color:var(--muted)}
.m-card.active p{color:rgba(255,255,255,.8)}

/* offering */
.offering{height:550px;background:linear-gradient(110deg,var(--violet) 0%,#7b56f2 55%,var(--blue) 100%);color:var(--white)}
.offering .ghost{left:0;width:1104px;text-align:center;top:26px;color:rgba(255,255,255,.12)}
.offering .h2{left:0;width:1104px;text-align:center;top:64px;color:var(--white)}
.offering .sub{left:0;width:1104px;text-align:center;top:130px;font-size:10px;font-weight:600}
.off-row{left:85px;top:165px;display:flex;gap:8px}
.o-card{width:233px;height:322px;border-radius:12px;padding:22px 16px}
.o-card.active{background:linear-gradient(160deg,var(--pink),var(--rose));box-shadow:0 12px 28px rgba(120,20,80,.35)}
.o-icon{width:88px;height:88px;border-radius:50%;border:2px solid var(--white);display:flex;align-items:center;justify-content:center;box-shadow:6px 6px 0 rgba(255,255,255,.35)}
.o-icon svg{width:46px;height:46px}
.o-card h3{font-size:13px;font-weight:700;margin:26px 0 8px}
.o-card p{font-size:9.5px;line-height:1.55;color:rgba(255,255,255,.8)}

/* careers */
.careers{height:408px}
.careers .ghost{left:85px;top:95px}
.careers .h2{left:85px;top:150px}
.careers .lead{left:85px;top:222px;width:430px;font-size:10.5px}
.btn{left:85px;top:296px;height:42px;width:158px;border-radius:21px;background:linear-gradient(90deg,var(--rose),var(--pink));color:var(--white);font-size:13px;font-weight:700;display:flex;align-items:center;justify-content:center;box-shadow:0 6px 14px rgba(240,50,110,.35)}
.careers-art{left:529px;top:85px;width:575px;height:323px;border-top-left-radius:120px;background:linear-gradient(135deg,#6a4ef0,var(--violet) 60%,#8a45f2)}

/* clients */
.clients{height:258px;background:var(--soft)}
.clients .h2{left:0;width:1104px;text-align:center;top:46px}
.client-row{left:60px;top:160px;width:984px;display:flex;justify-content:space-between}
.client{width:140px;text-align:center;font-size:12px;font-weight:800;color:#555560;letter-spacing:2px}
.client i{display:block;width:44px;height:44px;margin:0 auto 8px;border-radius:50%}

/* footer */
.footer{height:360px;background:linear-gradient(100deg,var(--footer-a),var(--footer-b));color:var(--white)}
.footer .brand{top:70px}
.footer .brand-name{font-size:40px}
.f-about{left:85px;top:200px;width:280px;font-size:9px;line-height:1.55;color:rgba(255,255,255,.75)}
.f-title{font-size:11px;font-weight:700}
.newsletter{left:465px;top:84px}
.field{margin-top:22px;width:292px;height:36px;border:1.5px solid rgba(255,255,255,.8);border-radius:18px;display:flex;align-items:center;justify-content:space-between;padding:0 3px 0 16px;font-size:8.5px;color:rgba(255,255,255,.8)}
.field b{background:var(--white);color:var(--footer-a);border-radius:15px;height:28px;width:96px;display:flex;align-items:center;justify-content:center;font-size:11px}
.follow{margin-top:16px}
.follow-row{display:flex;gap:8px;margin-top:10px}
.follow-row span{width:28px;height:28px;border-radius:50%;background:var(--white)}
.location{left:867px;top:84px}
.loc-item{display:flex;align-items:center;gap:10px;font-size:9px;color:rgba(255,255,255,.85);margin-top:14px}
.loc-item svg{width:12px;height:12px}
.rule{left:85px;top:285px;width:934px;height:1px;background:rgba(255,255,255,.3)}
.copy{left:85px;top:312px;font-size:9px;color:rgba(255,255,255,.85)}
.to-top{left:994px;top:302px;width:40px;height:40px;border-radius:50%;border:1.5px solid rgba(255,255,255,.8);display:flex;align-items:center;justify-content:center}
</style>
</head>
<body>
<div class="page">

  <header class="hero">
    <div class="abs topbar">
      <div class="social"><span></span><span></span><span></span><span></span></div>
      <div class="contact-line"><span>&#9993; info@vormal-iot.example</span><span>&#9742; 01-240-557-310</span></div>
    </div>
    <div class="abs brand">
      <div class="brand-name">VORMAL IoT</div>
    </div>
    <nav class="abs nav">
      <span class="active">Home</span><span>Our Methodology</span><span>Our Offering</span><span>Careers</span><span>Contact</span>
    </nav>
    <h1 class="abs hero-title">DATA SCIENCE</h1>
    <p class="abs hero-copy">Lorem ipsum dolor sit amet, consectetur adipiscing elit. Aenean et bibendum odio. Praesent sit amet bibendum nibh. Proin faucibus tincidunt mauris id euismod.</p>
    <div class="abs hero-art" role="img" aria-label="Isometric illustration of cloud servers, a laptop and people working with data charts"></div>
    <svg class="hero-curve" viewBox="0 0 1104 140" preserveAspectRatio="none" aria-hidden="true">
      <path d="M0 40 C 300 55, 600 85, 800 110 C 950 125, 1050 95, 1104 60 L1104 140 L0 140 Z" fill="#ffffff"/>
    </svg>
  </header>

  <section class="method">
    <div class="abs ghost">Methodology</div>
    <h2 class="abs h2">Our Methodology</h2>
    <p class="abs lead">Lorem ipsum dolor sit amet, consectetur adiping elit. Aenean et bibendum odio. Praesent sit amet bibendum nibh.</p>
    <p class="abs body">Lorem ipsum dolor sit amet, consectetur adipiscing elit. Aenean et bibendum odio. Praesent sit amet bibendum nibh. Proin faucibus tincidunt mauris id euismod. Donec sed sollicitudin velit. Etiam elit elit, faucibus non efficitur volutpat, eleifend quis nulla. Duis egestas neque id feugiat suscipit. Fusce nec enim at neque malesia lobortis in at leo. Proin sit amet eros at velit commodo interdum ut fermentum diam. Pellentesque est metus, congue quis lacinia vitae, feugiat lobortis lectus. Nunc lacinia turpis eget lobortis convallis.</p>
    <div class="abs method-grid">
      <div class="m-card active">
        <svg viewBox="0 0 36 36" fill="none" stroke="#fff" stroke-width="2"><circle cx="18" cy="18" r="4"/><circle cx="6" cy="6" r="3"/><circle cx="30" cy="6" r="3"/><circle cx="6" cy="30" r="3"/><circle cx="30" cy="30" r="3"/><path d="M8 8l7 7M28 8l-7 7M8 28l7-7M28 28l-7-7"/></svg>
        <h3>Lorem ipsum</h3>
        <p>Etiam elit elit, faucibus non efficitur volutpat, eleifend quis nulla. Duis egestas neque id</p>
      </div>
      <div class="m-card">
        <svg viewBox="0 0 36 36" fill="none" stroke="#8a4cf2" stroke-width="2"><rect x="4" y="6" width="28" height="22" rx="2"/><path d="M8 22l7-7 5 4 8-9"/></svg>
        <h3>Nunc fringilla</h3>
        <p>Etiam elit elit, faucibus non efficitur volutpat, eleifend quis nulla. Duis egestas neque id</p>
      </div>
      <div class="m-card">
        <svg viewBox="0 0 36 36" fill="none" stroke="#8a4cf2" stroke-width="2"><rect x="5" y="5" width="26" height="8" rx="2"/><rect x="5" y="15" width="26" height="8" rx="2"/><path d="M18 23v6M10 31h16"/></svg>
        <h3>Donec efficitur</h3>
        <p>Etiam elit elit, faucibus non efficitur volutpat, eleifend quis nulla. Duis egestas neque id</p>
      </div>
      <div class="m-card">
        <svg viewBox="0 0 36 36" fill="none" stroke="#8a4cf2" stroke-width="2"><ellipse cx="18" cy="8" rx="11" ry="4"/><path d="M7 8v20c0 2 5 4 11 4s11-2 11-4V8M7 18c0 2 5 4 11 4s11-2 11-4"/></svg>
        <h3>Quisque</h3>
        <p>Etiam elit elit, faucibus non efficitur volutpat, eleifend quis nulla. Duis egestas neque id</p>
      </div>
    </div>
  </section>

  <section class="offering">
    <div class="abs ghost">Offering</div>
    <h2 class="abs h2">Our Offering</h2>
    <p class="abs sub">Lorem ipsum dolor sit amet, consectetur adiping elit. Aenean et bibendum odio. Praesent sit amet bibendum nibh.</p>
    <div class="abs off-row">
      <div class="o-card">
        <div class="o-icon"><svg viewBox="0 0 46 46" fill="none" stroke="#fff" stroke-width="2"><path d="M12 28a8 8 0 0 1 2-15 11 11 0 0 1 20 3 6 6 0 0 1 0 12z"/><path d="M23 20v16M16 36h14"/></svg></div>
        <h3>Lorem ipsum</h3>
        <p>Fusce nec enim at neque malesia lobortis in at leo. Proin sit amet eros at velit commodo interdum ut fermentum. Pellentesque est metus, congue quis lacinia vitae, feugiat lobortis lectus. Nunc lacinia turpis eget lobortis convallis. Pellentesque est metus, congue quis lacinia vitae.</p>
      </div>
      <div class="o-card">
        <div class="o-icon"><svg viewBox="0 0 46 46" fill="none" stroke="#fff" stroke-width="2"><circle cx="12" cy="14" r="4"/><circle cx="34" cy="32" r="4"/><path d="M16 14h12a6 6 0 0 1 0 12H18a6 6 0 0 0 0 12"/></svg></div>
        <h3>Lorem ipsum</h3>
        <p>Fusce nec enim at neque malesia lobortis in at leo. Proin sit amet eros at velit commodo interdum ut fermentum. Pellentesque est metus, congue quis lacinia vitae, feugiat lobortis lectus. Nunc lacinia turpis eget lobortis convallis. Pellentesque est metus, congue quis lacinia vitae.</p>
      </div>
      <div class="o-card active">
        <div class="o-icon"><svg viewBox="0 0 46 46" fill="none" stroke="#fff" stroke-width="2"><ellipse cx="23" cy="12" rx="12" ry="5"/><path d="M11 12v22c0 3 5 5 12 5s12-2 12-5V12M11 23c0 3 5 5 12 5s12-2 12-5"/></svg></div>
        <h3>Lorem ipsum</h3>
        <p>Fusce nec enim at neque malesia lobortis in at leo. Proin sit amet eros at velit commodo interdum ut fermentum. Pellentesque est metus, congue quis lacinia vitae, feugiat lobortis lectus. Nunc lacinia turpis eget lobortis convallis. Pellentesque est metus, congue quis lacinia vitae.</p>
      </div>
      <div class="o-card">
        <div class="o-icon"><svg viewBox="0 0 46 46" fill="none" stroke="#fff" stroke-width="2"><circle cx="23" cy="23" r="13"/><path d="M23 10v13h13M23 23l-9 9"/></svg></div>
        <h3>Lorem ipsum</h3>
        <p>Fusce nec enim at neque malesia lobortis in at leo. Proin sit amet eros at velit commodo interdum ut fermentum. Pellentesque est metus, congue quis lacinia vitae, feugiat lobortis lectus. Nunc lacinia turpis eget lobortis convallis. Pellentesque est metus, congue quis lacinia vitae.</p>
      </div>
    </div>
  </section>

  <section class="careers">
    <div class="abs ghost">Careers</div>
    <h2 class="abs h2">Careers</h2>
    <p class="abs lead">Mauris a sem vehicula, sollicitudin velit vel, venenatis tortor. Suspendisse luctus dolor ac sagittis blandit. Nulla erat ante, interdum sed elementum non, aliquet nec arcu.</p>
    <div class="abs btn">Apply Now</div>
    <div class="abs careers-art" role="img" aria-label="Isometric illustration of laptops with code on screen"></div>
  </section>

  <section class="clients">
    <h2 class="abs h2">Worldwide Clients</h2>
    <div class="abs client-row">
      <div class="client"><i style="background:#f0763a"></i>LOREM</div>
      <div class="client"><i style="background:#43b8c9"></i>LOREM</div>
      <div class="client"><i style="background:#2fb58c"></i>LOREM</div>
      <div class="client"><i style="background:#f2b632"></i>LOREM</div>
      <div class="client"><i style="background:#6fa845"></i>LOREM</div>
      <div class="client"><i style="background:#1f9a8a"></i>LOREM</div>
    </div>
  </section>

  <footer class="footer">
    <div class="abs brand">
      <div class="brand-name">VORMAL IoT</div>
    </div>
    <p class="abs f-about">Lorem ipsum dolor sit amet, consectetur adipiscing elit. Aenean et bibendum odio. Praesent sit amet bibendum nibh. Proin faucibus tincidunt mauris id euismod. Donec sed sollicitudin velit. Etiam elit elit, faucibus non efficitur volutpat, eleifend quis nulla.</p>
    <div class="abs newsletter">
      <div class="f-title">Subscribe To Newsletter</div>
      <div class="field"><span>&#9993; Enter your email address</span><b>Submit</b></div>
      <div class="f-title follow">Follow Us</div>
      <div class="follow-row"><span></span><span></span><span></span><span></span></div>
    </div>
    <div class="abs location">
      <div class="f-title">Our Location</div>
      <div class="loc-item"><svg viewBox="0 0 12 12"><path d="M6 1a3.5 3.5 0 0 1 3.5 3.5C9.5 7 6 11 6 11S2.5 7 2.5 4.5A3.5 3.5 0 0 1 6 1z" fill="#fff"/></svg>45 BC, making it over 2000</div>
      <div class="loc-item"><svg viewBox="0 0 12 12"><rect x="1" y="3" width="10" height="7" rx="1" fill="#fff"/></svg>info@vormal-iot.example</div>
      <div class="loc-item"><svg viewBox="0 0 12 12"><path d="M3 1l2 2-1 2a6 6 0 0 0 3 3l2-1 2 2-1 2C5 11 1 7 1 3z" fill="#fff"/></svg>01-240-557-310</div>
    </div>
    <div class="abs rule"></div>
    <div class="abs copy">© 2019 VORMAL IoT. All Right Reserved.</div>
    <div class="abs to-top"><svg width="14" height="8" viewBox="0 0 14 8" fill="none" stroke="#fff" stroke-width="1.5"><path d="M1 7l6-6 6 6"/></svg></div>
  </footer>

</div>
</body>
</html>
```